Outdoor Real Estate Sales Banner

It should say

248 Wexcombe Street, East Boston
Coming Spring 2026
3 Luxury Condos
Experience refined living with elegant design and high-end finishes. Thoughtfully crafted for both comfort and sophistication.
Construction by V Construction
Now Accepting Reservations

Schedule Your Private Tour Today
Marisol Thibault, Fenwick Realty | 617-555-0142 | Marisol@fenwickharbor.com
Gregory Hale, Fenwick Realty | 617-555-0187 | Gregory@fenwickharbor.com

Target Market(s)

30-45

Industry/Entity Type

real estate

Font styles to use
Serif

Requirements
Must have
• Colors of logo and preppy rich look
Nice to have
• herringbone incorporated the pattern
Should not have
• any loud colors

```html
<!DOCTYPE html>
<html lang="en">
<head>
<meta charset="utf-8">
<title>248 Wexcombe Street – Outdoor Banner</title>
<link href="https://fonts.googleapis.com/css2?family=Lora:wght@400;500&family=Poppins:wght@400;500;600&family=League+Spartan:wght@500&display=swap" rel="stylesheet">
<style>
  :root {
    --navy: #2c3c5d;
    --gold: #dcb46e;
    --gold-soft: #e1b976;
    --white: #ffffff;
    --facade-light: #e8d3a0;
    --facade-mid: #d9bf85;
    --photo-tone: #8a8a86;
  }
  * { margin: 0; padding: 0; box-sizing: border-box; }
  html, body { width: 1200px; height: 2400px; overflow: hidden; background: var(--navy); }
  .banner {
    position: relative; width: 1200px; height: 2400px; overflow: hidden;
    background: var(--navy);
    font-family: "Poppins", sans-serif;
  }
  .hero-shapes { position: absolute; left: 0; top: 0; }
  .brand-name {
    position: absolute; left: 45px; top: 1020px; width: 400px; text-align: center;
    font-family: "Lora", serif; font-weight: 400; font-size: 42px; line-height: 1;
    color: var(--gold);
  }
  .centered { position: absolute; left: 0; width: 1200px; text-align: center; line-height: 1; font-weight: 400; }
  .address { top: 1176px; font-family: "Lora", serif; font-weight: 400; font-size: 90px; color: var(--gold); }
  .neighborhood { top: 1282px; font-family: "League Spartan", sans-serif; font-weight: 500; font-size: 54px; color: var(--white); }
  .rule { position: absolute; height: 2px; background: var(--gold); }
  .rule-top { left: 216px; width: 776px; top: 1372px; }
  .rule-mid { left: 211px; width: 774px; top: 1794px; }
  .rule-low { left: 211px; width: 774px; top: 1892px; }
  .rule-foot { left: 120px; width: 959px; top: 2234px; height: 3px; }
  .unit-count { top: 1411px; font-family: "Lora", serif; font-weight: 400; font-size: 82px; color: var(--gold); }
  .launch { top: 1510px; font-family: "Poppins", sans-serif; font-weight: 500; font-size: 42px; color: var(--white); }
  .pitch { top: 1588px; font-size: 26px; line-height: 39px; color: var(--gold); }
  .builder { top: 1710px; font-family: "Lora", serif; font-size: 38px; color: var(--white); }
  .reservations { top: 1825px; font-family: "Lora", serif; font-weight: 400; font-size: 54px; color: var(--gold); }
  .tour-call { top: 1911px; font-family: "Lora", serif; font-size: 54px; color: var(--white); }
  .agent { position: absolute; top: 2050px; height: 132px; }
  .agent-left { left: 67px; }
  .agent-right { left: 638px; }
  .agent-photo { position: absolute; left: 0; top: 0; width: 110px; height: 132px; }
  .agent-info { position: absolute; left: 128px; top: 0; white-space: nowrap; color: var(--white); font-size: 21px; line-height: 29.5px; }
  .agent-name { font-family: "Lora", serif; font-size: 40px; line-height: 1; color: var(--gold); margin-bottom: 4px; }
  .agent-divider { position: absolute; left: 599px; top: 2060px; width: 2px; height: 112px; background: var(--gold); }
  .website { top: 2250px; font-family: "Poppins", sans-serif; font-weight: 600; font-size: 23px; letter-spacing: 6px; color: var(--white); }
</style>
</head>
<body>
<main class="banner">
  <svg class="hero-shapes" width="1200" height="1300" viewBox="0 0 1200 1300">
    <circle cx="802" cy="427" r="717" fill="var(--gold-soft)"/>
    <circle cx="792" cy="457" r="648" fill="var(--white)"/>
    <defs>
      <linearGradient id="facadeTone" x1="0" y1="0" x2="1" y2="1">
        <stop offset="0" stop-color="var(--facade-light)"/>
        <stop offset="1" stop-color="var(--facade-mid)"/>
      </linearGradient>
    </defs>
    <rect x="404" y="88" width="762" height="815" fill="url(#facadeTone)" role="img" aria-label="Architectural south elevation drawing of the three-storey condominium building with clapboard siding, white-trimmed windows and front entry stair"/>
  </svg>

  <div class="brand-name">Fenwick Realty</div>

  <h1 class="centered address">248 Wexcombe Street</h1>
  <div class="centered neighborhood">East Boston</div>
  <div class="rule rule-top"></div>

  <h2 class="centered unit-count">3 Luxury Condominiums</h2>
  <div class="centered launch">Coming Spring 2026</div>
  <p class="centered pitch">Experience refined living with elegant design and high-end finishes.<br>Thoughtfully crafted residences that balance comfort, sophistication,<br>and timeless New England character.</p>
  <div class="centered builder">Construction by V Construction</div>

  <div class="rule rule-mid"></div>
  <div class="centered reservations">NOW ACCEPTING RESERVATIONS</div>
  <div class="rule rule-low"></div>
  <div class="centered tour-call">Schedule Your Private Tour Today</div>

  <section class="agent agent-left">
    <svg class="agent-photo" width="110" height="132" role="img" aria-label="Portrait photo of agent Marisol Thibault">
      <rect width="110" height="132" fill="var(--photo-tone)"/>
    </svg>
    <div class="agent-info">
      <div class="agent-name">Marisol Thibault</div>
      <div>Fenwick Realty</div>
      <div>617-555-0142</div>
      <div>Marisol@fenwickharbor.com</div>
    </div>
  </section>
  <div class="agent-divider"></div>
  <section class="agent agent-right">
    <svg class="agent-photo" width="110" height="132" role="img" aria-label="Portrait photo of agent Gregory Hale">
      <rect width="110" height="132" fill="var(--photo-tone)"/>
    </svg>
    <div class="agent-info">
      <div class="agent-name">Gregory Hale</div>
      <div>Fenwick Realty</div>
      <div>617-555-0187</div>
      <div>Gregory@fenwickharbor.com</div>
    </div>
  </section>

  <div class="rule rule-foot"></div>
  <div class="centered website">WWW.FENWICKHARBOR.COM</div>
</main>
</body>
</html>
```